BOLD & MINIMALIST DESIGN NEEDED

We want a very bold but minimalistic business card design that is impactful and utilizes both sides of the business card. Our current logo is included for your use.

We want bold fonts and good use of negative space. We don't want the logo to overpower the design.

Target Market(s)

Professionals who are building new commercial buildings.

Industry/Entity Type

Construction

Contact Information for Business Card

Name, Title, email, office phone, cell phone, website

Font styles to use
Serif
Sans Serif

Requirements
Must have
• Bold design!

```html
<!DOCTYPE html>
<html lang="en">
<head>
<meta charset="utf-8">
<title>Ridgeline Design + Build — Business Card</title>
<link href="https://fonts.googleapis.com/css2?family=Montserrat:wght@400;500;800&display=swap" rel="stylesheet">
<style>
  :root{
    --stage:#2b2b2b;
    --ink:#111111;
    --green:#7cc242;
    --green-light:#dcedc4;
    --green-mid:#b4da84;
    --paper:#ffffff;
    --muted:#333333;
  }
  html,body{margin:0;padding:0;overflow:hidden;}
  body{
    width:1200px;height:875px;
    background:var(--stage);
    display:flex;flex-direction:column;align-items:center;justify-content:center;gap:56px;
    font-family:"Montserrat",Arial,sans-serif;
  }
  .card{
    width:560px;height:320px;border-radius:22px;
    box-shadow:0 14px 30px rgba(0,0,0,.45);
    position:relative;box-sizing:border-box;
  }
  .card--front{
    background:linear-gradient(115deg,var(--green-light) 0%,var(--green-mid) 70%,#aed67a 100%);
    display:flex;align-items:center;justify-content:center;
  }
  .card--back{
    background:var(--paper);
    display:flex;align-items:center;padding:0 40px 0 56px;
  }
  .brand{
    display:flex;align-items:center;gap:14px;color:var(--ink);
    font-weight:800;text-transform:uppercase;line-height:1;
  }
  .brand__mark{width:22px;height:22px;background:var(--ink);flex:none;}
  .brand__name{display:flex;flex-direction:column;}
  .brand__primary{letter-spacing:.5px;}
  .brand__secondary{letter-spacing:6px;margin-top:8px;}
  .card--front .brand__primary{font-size:52px;}
  .card--front .brand__secondary{font-size:18px;}
  .card--front .brand__mark{width:30px;height:30px;}
  .card--back .brand__primary{font-size:28px;}
  .card--back .brand__secondary{font-size:10px;letter-spacing:3.4px;margin-top:5px;}
  .card--back .brand__mark{width:16px;height:16px;}
  .divider{width:2px;height:128px;background:var(--green);margin:0 26px 0 24px;flex:none;}
  .contact{color:var(--ink);}
  .contact__name{font-weight:800;font-size:20px;margin:0;}
  .contact__title{font-weight:400;font-size:12px;margin:2px 0 12px;color:var(--muted);}
  .contact__list{list-style:none;margin:0;padding:0;}
  .contact__item{display:flex;align-items:center;gap:8px;font-size:12px;font-weight:500;margin:4px 0;}
  .contact__icon{width:12px;height:12px;flex:none;fill:var(--green);}
</style>
</head>
<body>

<section class="card card--front" aria-label="Card front">
  <div class="brand">
    <span class="brand__mark"></span>
    <span class="brand__name">
      <span class="brand__primary">Ridgeline</span>
      <span class="brand__secondary">Design + Build</span>
    </span>
  </div>
</section>

<section class="card card--back" aria-label="Card back">
  <div class="brand">
    <span class="brand__mark"></span>
    <span class="brand__name">
      <span class="brand__primary">Ridgeline</span>
      <span class="brand__secondary">Design + Build</span>
    </span>
  </div>
  <div class="divider"></div>
  <div class="contact">
    <p class="contact__name">Daniel Moreau</p>
    <p class="contact__title">CEO &amp; Founder</p>
    <ul class="contact__list">
      <li class="contact__item">
        <svg class="contact__icon" viewBox="0 0 24 24"><path d="M6.6 10.8a15 15 0 0 0 6.6 6.6l2.2-2.2c.3-.3.7-.4 1-.2 1.1.4 2.3.6 3.6.6.6 0 1 .4 1 1V20c0 .6-.4 1-1 1A17 17 0 0 1 3 4c0-.6.4-1 1-1h3.5c.6 0 1 .4 1 1 0 1.3.2 2.5.6 3.6.1.3 0 .7-.2 1z"/></svg>
        (555) 214-0390
      </li>
      <li class="contact__item">
        <svg class="contact__icon" viewBox="0 0 24 24"><path d="M3 9c0-2 4-4 9-4s9 2 9 4v2h-5V9H8v2H3zM6 12h12l2 8H4zm6 2a2.5 2.5 0 1 0 0 5 2.5 2.5 0 0 0 0-5z"/></svg>
        1-800-555-0147
      </li>
      <li class="contact__item">
        <svg class="contact__icon" viewBox="0 0 24 24"><path d="M2 5h20v14H2zm2 2v.5l8 5.5 8-5.5V7l-8 5.5z"/></svg>
        info@ridgelinebuild.com
      </li>
      <li class="contact__item">
        <svg class="contact__icon" viewBox="0 0 24 24"><circle cx="12" cy="12" r="10"/></svg>
        www.ridgelinebuild.com
      </li>
    </ul>
  </div>
</section>

</body>
</html>
```